Veltrano.co - Polar Expeditions Specialists

We need a modern, visually striking business card for Veltrano.co, a company specialized in selling expedition cruises to the most remote regions on Earth, with a focus on the Arctic and Antarctica. The design should instantly communicate that the cardholder is an expert in polar travel. Use clean, premium aesthetics with cool tones like icy blue and white, possibly incorporating polar imagery (ice, glaciers, penguins, etc.)

Attached the logo

Contact Information for Business Card

Feels high-end and trustworthy.. Visually memorable — encourages people to keep it

Colors
0054AA
0677BA
7BADD7
CADEEF
E8F1F8

Requirements
Must have
• ice, glaciers, penguins, montains
Nice to have
• modern, transparente,

```html
<!DOCTYPE html>
<html lang="en">
<head>
<meta charset="utf-8">
<title>Veltrano.co – Business Card</title>
<link href="https://fonts.googleapis.com/css2?family=Poppins:wght@400;600;700&display=swap" rel="stylesheet">
<style>
  :root {
    --bg: #3a3a3a;
    --card: #151515;
    --blue: #2f78c4;
    --white: #f2f2f2;
    --pattern-dark: #0d0d0d;
    --pattern-light: #5a5a5a;
  }
  * { box-sizing: border-box; margin: 0; padding: 0; }
  html, body {
    width: 1200px; height: 791px; overflow: hidden;
    background: var(--bg);
    font-family: "Poppins", Arial, sans-serif;
  }
  .stage {
    width: 1200px; height: 791px;
    display: flex; align-items: center; justify-content: center; gap: 40px;
  }
  .card {
    position: relative;
    width: 540px; height: 309px;
    background: var(--card);
    border-bottom: 2px solid var(--blue);
    border-left: 2px solid var(--blue);
    overflow: hidden;
  }
  .brand {
    display: flex; align-items: center; gap: 12px;
  }
  .brand-dot {
    width: 34px; height: 34px; border-radius: 50%;
    background: var(--blue); flex-shrink: 0;
  }
  .brand-name {
    color: var(--blue); font-weight: 700; font-size: 30px; line-height: 1;
  }
  .brand-tagline {
    color: var(--blue); font-weight: 600; font-size: 9.5px; margin-top: 4px;
  }
  /* front */
  .card-front .brand {
    position: absolute; left: 52px; top: 150px;
  }
  .divider {
    position: absolute; left: 290px; top: 110px;
    width: 1.5px; height: 96px; background: var(--blue);
  }
  .contact {
    position: absolute; left: 316px; top: 100px;
  }
  .contact-name {
    color: var(--blue); font-weight: 700; font-size: 17px; letter-spacing: 0.3px;
  }
  .contact-role {
    color: var(--white); font-size: 12px; margin-bottom: 12px;
  }
  .contact-line {
    display: flex; align-items: center; gap: 8px;
    color: var(--white); font-size: 12px; line-height: 20px;
  }
  .contact-line svg { width: 11px; height: 11px; fill: var(--blue); flex-shrink: 0; }
  /* back */
  .pattern {
    position: absolute; inset: 0;
    background: linear-gradient(120deg, var(--pattern-dark) 0%, #1b1b1b 40%, #3a3a3a 70%, var(--pattern-light) 100%);
  }
  .card-back .brand {
    position: absolute; left: 258px; top: 138px;
    background: rgba(21,21,21,0.85); padding: 8px 10px;
  }
</style>
</head>
<body>
<main class="stage">
  <section class="card card-front">
    <div class="brand">
      <span class="brand-dot"></span>
      <div>
        <div class="brand-name">Veltrano.co</div>
        <div class="brand-tagline">Polar Expeditions Specialists</div>
      </div>
    </div>
    <span class="divider"></span>
    <div class="contact">
      <div class="contact-name">MARCUS ORLEN</div>
      <div class="contact-role">President</div>
      <div class="contact-line">
        <svg viewBox="0 0 24 24"><path d="M6.6 10.8a15.1 15.1 0 0 0 6.6 6.6l2.2-2.2a1 1 0 0 1 1-.25 11.4 11.4 0 0 0 3.6.6 1 1 0 0 1 1 1V20a1 1 0 0 1-1 1A17 17 0 0 1 3 4a1 1 0 0 1 1-1h3.5a1 1 0 0 1 1 1c0 1.25.2 2.45.6 3.6a1 1 0 0 1-.25 1z"/></svg>
        555-310-4872
      </div>
      <div class="contact-line">
        <svg viewBox="0 0 24 24"><path d="M2 5h20v14H2z M2 5l10 8 10-8" /></svg>
        marcusorlen@veltrano.co
      </div>
      <div class="contact-line">
        <svg viewBox="0 0 24 24"><circle cx="12" cy="12" r="10"/></svg>
        www.veltrano.co
      </div>
    </div>
  </section>

  <section class="card card-back">
    <div class="pattern" role="img" aria-label="Repeating pattern of polar bear silhouettes fading from black to grey"></div>
    <div class="brand">
      <span class="brand-dot"></span>
      <div>
        <div class="brand-name">Veltrano.co</div>
        <div class="brand-tagline">Polar Expeditions Specialists</div>
      </div>
    </div>
  </section>
</main>
</body>
</html>
```